Business card update

Opening a subsidiary of my company in the USA and need to update my logo.
Updates

Reason: Give more time to a good design.

I made a mistake on my briefing. It's only the business card. Thanks for alerting me on the mistake.

All the best

Teodoro

Target Market(s)

We are an Executive Search company and our target audience are executives in large corporations.

Industry/Entity Type

Business

Requirements
Must have
• Keep the logo. In the US the company is called Delia Brunet Executive Search.

```html
<!DOCTYPE html>
<html lang="en">
<head>
<meta charset="utf-8">
<title>Delia Brunet Executive Search – Business Card</title>
<link rel="stylesheet" href="https://fonts.googleapis.com/css2?family=Josefin+Sans:wght@300;400&family=Questrial&display=swap">
<style>
  :root {
    --stage: #5b6a6b;
    --card: #ffffff;
    --mint: #4fe3b0;
    --navy: #2c3a68;
    --ink: #2a2a2a;
    --alert: #e0261d;
  }
  * { margin: 0; padding: 0; box-sizing: border-box; }
  html, body {
    width: 1200px; height: 741px; overflow: hidden;
    background: var(--stage);
  }
  .canvas { position: relative; width: 1200px; height: 741px; }
  .card {
    position: absolute; left: 150px; top: 110px;
    width: 900px; height: 521px;
    background: var(--card);
    overflow: hidden;
  }
  .brand-name {
    position: absolute; right: 32px; top: 52px;
    font-family: "Questrial", sans-serif; font-weight: 400;
    font-size: 40px; color: var(--navy); line-height: 1;
    white-space: nowrap;
  }
  .name-band {
    position: absolute; left: 0; top: 157px;
    width: 100%; height: 86px;
    background: var(--mint);
  }
  .person-name {
    position: absolute; left: 43px; top: 194px;
    font-family: "Questrial", sans-serif; font-weight: 400;
    font-size: 37px; color: #ffffff; line-height: 1;
    white-space: nowrap;
  }
  .phone {
    position: absolute; left: 43px; top: 254px;
    display: flex; align-items: center; gap: 10px;
    font-family: "Questrial", sans-serif; font-size: 29px;
    color: var(--ink); white-space: nowrap;
  }
  .phone svg { width: 26px; height: 26px; }
  .company-line {
    position: absolute; left: 10px; right: 10px; top: 382px;
    display: flex; align-items: center; gap: 14px;
  }
  .company-line .rule { flex: 1; height: 2px; background: var(--mint); opacity: 0.7; }
  .company-name {
    font-family: "Josefin Sans", sans-serif; font-weight: 300;
    font-size: 46px; letter-spacing: 2px; color: var(--mint);
    line-height: 1; white-space: nowrap;
  }
  .address, .web {
    position: absolute; top: 447px;
    font-family: "Josefin Sans", sans-serif; font-weight: 400;
    font-size: 22px; line-height: 31px; color: var(--ink);
    font-style: normal; white-space: nowrap;
  }
  .address { left: 43px; }
  .web { right: 32px; text-align: right; }
</style>
</head>
<body>
<main class="canvas">
  <section class="card">
    <p class="brand-name">Delia Brunet</p>

    <div class="name-band"></div>
    <h1 class="person-name">Teodoro S. Brunet</h1>

    <p class="phone">
      <svg viewBox="0 0 24 24" aria-hidden="true">
        <path fill="var(--alert)" d="M6.6 10.8c1.4 2.8 3.8 5.1 6.6 6.6l2.2-2.2c.3-.3.7-.4 1-.2 1.1.4 2.3.6 3.6.6.6 0 1 .4 1 1V20c0 .6-.4 1-1 1C10.6 21 3 13.4 3 4c0-.6.4-1 1-1h3.5c.6 0 1 .4 1 1 0 1.3.2 2.5.6 3.6.1.3 0 .7-.2 1z"/>
      </svg>
      305 555-0148
    </p>

    <div class="company-line">
      <span class="rule"></span>
      <span class="company-name">Delia Brunet Executive Search</span>
      <span class="rule"></span>
    </div>

    <address class="address">
      4870 Harbor Point Ave Suite 310<br>
      Coral Bay FL 33190
    </address>
    <p class="web">
      www.dbexecutivesearch.com<br>
      tbrunet@dbexecutivesearch.com
    </p>
  </section>
</main>
</body>
</html>
```